Brindle Sky Port needs a new upscale business card design for our high end aircraft hangar complex

Brindle Sky Port (BSP) is a large, upscale jet hangar complex in the US housing expensive aircraft. We need a new business card design, using our current logo. We will be attending a industry convention and need a card design that will stand out and be remembered by aircraft owners and private pilots.

Target Market(s)

Aircraft pilots or owners looking for a new upscale hangar

Industry/Entity Type

Airport

Contact Information for Business Card

I like to use very heavy card stock, 400#, double sided. Square, no rounded edges please.

Colors
3276b5
0255a3
85abd2

Requirements
Must have
• An expensive, classy design, vivid colors.
Nice to have
• Needs to look very expensive and classy, and have some "pop". Designer must be able to download or copy my current typeface or fonts.
• One card side might be black with the "Logo and Brindle Sky Port Double line image in blue (or try gold, or glossy black), and perhaps have a grayed out "K720 jet silhouette". The other card side would have our contact info, and perhaps the "BSP Logo only". I'd like my contact info 'stacked', not in a paragraph format.
Should not have
• Should not look "too busy". Having a double-sided card will help.

```html
<!DOCTYPE html>
<html lang="en">
<head>
<meta charset="utf-8">
<title>Brindle Sky Port – Business Card</title>
<link rel="stylesheet" href="https://fonts.googleapis.com/css2?family=Roboto:wght@400;700;900&display=swap">
<style>
  :root {
    --bg: #3b3430;
    --card: #1b1c1e;
    --card-edge: #0f1011;
    --silver: #b9bcc0;
    --blue: #3276b5;
    --blue-deep: #0255a3;
    --blue-light: #85abd2;
    --text: #e9eaec;
    --divider: #6c6f73;
  }
  * { margin: 0; padding: 0; box-sizing: border-box; }
  html, body {
    width: 1200px; height: 787px; overflow: hidden;
    background: var(--bg);
    font-family: "Roboto", Arial, sans-serif;
  }
  .canvas {
    width: 1200px; height: 787px;
    display: flex; align-items: center; justify-content: center; gap: 60px;
  }
  .card {
    width: 525px; height: 300px;
    background: var(--card);
    box-shadow: 0 10px 30px rgba(0,0,0,.45);
    position: relative;
  }
  /* Front side */
  .card-front {
    display: flex; flex-direction: column; align-items: center; justify-content: center;
  }
  .brand-mark {
    display: flex; align-items: center; gap: 12px;
  }
  .brand-square {
    width: 22px; height: 22px; background: var(--silver);
  }
  .brand-name {
    font-weight: 900; font-size: 34px; letter-spacing: 1px;
    text-transform: uppercase; color: var(--silver);
  }
  .front-web {
    margin-top: 26px; font-size: 14px; letter-spacing: 3px; color: var(--text);
  }
  /* Back side */
  .card-back {
    display: flex; align-items: center; padding: 0 28px 0 34px;
  }
  .back-brand {
    width: 215px; display: flex; justify-content: center;
  }
  .back-brand .brand-name {
    color: var(--blue); font-size: 25px; line-height: 1.05; text-align: center;
  }
  .divider {
    width: 1px; height: 210px; background: var(--divider); margin: 0 22px 0 10px;
  }
  .contact { color: var(--text); font-size: 13.5px; line-height: 1.4; }
  .contact-name { color: var(--blue); font-size: 18px; font-weight: 400; }
  .contact-title { font-size: 15px; margin-bottom: 8px; }
  .contact-address { margin-bottom: 8px; }
  .contact-list { list-style: none; }
  .contact-list li { display: flex; align-items: center; gap: 10px; }
  .contact-list svg { width: 13px; height: 13px; fill: var(--blue); flex: none; }
  .contact-web { padding-left: 23px; }
</style>
</head>
<body>
<main class="canvas">
  <section class="card card-front" aria-label="Card front">
    <div class="brand-mark">
      <span class="brand-square"></span>
      <span class="brand-name">Brindle Sky Port</span>
    </div>
    <p class="front-web">www.brindleskyport.com</p>
  </section>

  <section class="card card-back" aria-label="Card back">
    <div class="back-brand">
      <span class="brand-name">Brindle<br>Sky Port</span>
    </div>
    <div class="divider"></div>
    <div class="contact">
      <p class="contact-name">Carter Wells</p>
      <p class="contact-title">President</p>
      <p class="contact-address">4120 Harlow Ridge Road<br>Kestrel Bay, NY 11920</p>
      <ul class="contact-list">
        <li>
          <svg viewBox="0 0 16 16" aria-hidden="true"><path d="M3 1h3l1.5 4-2 1.3a9 9 0 0 0 4.2 4.2L11 8.5l4 1.5v3a2 2 0 0 1-2 2A13 13 0 0 1 1 3a2 2 0 0 1 2-2z"/></svg>
          555 0142 7781
        </li>
        <li>
          <svg viewBox="0 0 16 16" aria-hidden="true"><path d="M4 0h8a1 1 0 0 1 1 1v14a1 1 0 0 1-1 1H4a1 1 0 0 1-1-1V1a1 1 0 0 1 1-1zm1 2v10h6V2zm3 11a1 1 0 1 0 0 2 1 1 0 0 0 0-2z"/></svg>
          555 0187 3364
        </li>
        <li>
          <svg viewBox="0 0 16 16" aria-hidden="true"><path d="M4 0h7v4H4zM1 5h14v8h-2v3H3v-3H1zm4 6v3h6v-3z"/></svg>
          555 0163 9025
        </li>
        <li>
          <svg viewBox="0 0 16 16" aria-hidden="true"><circle cx="8" cy="8" r="8"/><path d="M4 5h8v6H4z" fill="#1b1c1e"/><path d="M4 5l4 3 4-3" stroke="#3276b5" fill="none"/></svg>
          carter@brindleskyport.com
        </li>
        <li class="contact-web">www.brindleskyport.com</li>
      </ul>
    </div>
  </section>
</main>
</body>
</html>
```